Vibrant, yet professional, stationery set and other designs required.

I need to source a fantastic designer for a new project as part of my company using a new logo designed via sketch harbor.

**UPDATE** I am not looking for just 'fine' design that will suffice. I am looking for something great.

We are a life assurance brokerage based in Dublin, Ireland and BrightRoost.ie is our new website aimed at providing services for young families in Ireland. We are hoping to be the 'Velro' level of service providers in this area and I am looking for the quality of design to reflect this :-) Hopefully that makes sense!

I have a preference for straight lines over curves and waves.

I need...

1. Business card
2. Letterhead
3. Banner (for printing - 76cm X 305cm)
4. Car branding for KORVA 9 (2014 sport model) I believe the templates are freely available online.

Target Market(s)

Parents in Ireland - Aged 27 to 50.

Industry/Entity Type

Financial Planning

Colors

Designer to choose colors to be used in the design.

Requirements
Must have
• All of the items listed in the description above. I like clean, bright, legible, vibrant and professional design.
Should not have
• No silly or 'cheap' looking designs. This is a professional company looking to provide a professional service.

```html
<!DOCTYPE html>
<html lang="en">
<head>
<meta charset="utf-8">
<title>BrightRoost.ie Business Card</title>
<link href="https://fonts.googleapis.com/css2?family=Roboto:wght@400;500;700&display=swap" rel="stylesheet">
<style>
  :root {
    --backdrop: #b9b9b9;
    --brand-orange: #ef8019;
    --brand-green: #8dbb3f;
    --brand-blue: #6cc4e6;
    --brand-grey: #8e979b;
    --card-white: #f7f7f7;
    --text-grey: #555a5d;
  }
  * { margin: 0; padding: 0; box-sizing: border-box; }
  html, body { width: 1200px; height: 960px; overflow: hidden; }
  body {
    position: relative;
    background: var(--backdrop);
    font-family: "Roboto", Arial, sans-serif;
  }
  .card {
    position: absolute;
    left: 320px;
    width: 600px;
  }
  .card--front {
    top: 105px;
    height: 335px;
    background: var(--brand-orange);
  }
  .card--back {
    top: 493px;
    height: 342px;
    background: var(--card-white);
  }
  .wordmark {
    position: absolute;
    left: 0;
    right: 0;
    text-align: center;
    font-weight: 700;
    letter-spacing: -1px;
    line-height: 1;
  }
  .card--front .wordmark {
    top: 138px;
    font-size: 56px;
    color: #fff;
  }
  .card--back .wordmark {
    top: 80px;
    font-size: 56px;
    color: var(--brand-grey);
  }
  .colour-rule {
    position: absolute;
    top: 205px;
    left: 30px;
    display: flex;
    gap: 5px;
  }
  .colour-rule span {
    display: block;
    width: 130px;
    height: 3px;
  }
  .colour-rule .green { background: var(--brand-green); }
  .colour-rule .orange { background: var(--brand-orange); }
  .colour-rule .blue { background: var(--brand-blue); }
  .colour-rule .grey { background: var(--brand-grey); width: 132px; }
  .holder {
    position: absolute;
    left: 28px;
    top: 222px;
  }
  .holder__name {
    font-size: 19px;
    font-weight: 500;
    color: var(--brand-orange);
    line-height: 24px;
  }
  .holder__role {
    font-size: 14px;
    color: var(--brand-grey);
    line-height: 22px;
  }
  .holder__address {
    margin-top: 11px;
    font-size: 14px;
    color: var(--text-grey);
    line-height: 19px;
    font-style: normal;
  }
  .contacts {
    position: absolute;
    right: 28px;
    top: 220px;
    list-style: none;
  }
  .contacts li {
    display: flex;
    justify-content: flex-end;
    align-items: center;
    gap: 8px;
    font-size: 14px;
    color: var(--text-grey);
    line-height: 19px;
  }
  .contacts svg {
    width: 12px;
    height: 12px;
    fill: var(--brand-orange);
    flex: none;
  }
</style>
</head>
<body>

<section class="card card--front">
  <p class="wordmark">brightroost.ie</p>
</section>

<section class="card card--back">
  <p class="wordmark">brightroost.ie</p>

  <div class="colour-rule">
    <span class="green"></span><span class="orange"></span><span class="blue"></span><span class="grey"></span>
  </div>

  <div class="holder">
    <p class="holder__name">AOIFE BRENNAN</p>
    <p class="holder__role">CEO/FOUNDER</p>
    <address class="holder__address">14 Harcourt Row<br>Dublin 2, D02 KX71</address>
  </div>

  <ul class="contacts">
    <li>614 203 5871
      <svg viewBox="0 0 12 12"><path d="M2.5 0.5 L4.5 0.5 L5.2 3.2 L3.9 4.3 Q5 6.8 7.7 8.1 L8.8 6.8 L11.5 7.5 L11.5 9.5 Q11.5 11.5 9.5 11.5 Q0.5 10.5 0.5 2.5 Q0.5 0.5 2.5 0.5 Z"/></svg>
    </li>
    <li>872 519 4630
      <svg viewBox="0 0 12 12"><path d="M3 0 H9 Q10 0 10 1 V11 Q10 12 9 12 H3 Q2 12 2 11 V1 Q2 0 3 0 Z M3.2 1.5 V9.5 H8.8 V1.5 Z M5.3 10 H6.7 V11.2 H5.3 Z"/></svg>
    </li>
    <li>459 730 2186
      <svg viewBox="0 0 12 12"><path d="M3 0.5 H9 V3.5 H3 Z M0.5 4.5 H11.5 V9 H9.5 V7.5 H2.5 V9 H0.5 Z M3.2 8.3 H8.8 V11.5 H3.2 Z"/></svg>
    </li>
    <li>aoife@brightroost.ie
      <svg viewBox="0 0 12 12"><path d="M0.5 2.5 H11.5 V3.2 L6 6.8 L0.5 3.2 Z M0.5 4.4 L6 8 L11.5 4.4 V9.5 H0.5 Z"/></svg>
    </li>
    <li>www.brightroost.ie
      <svg viewBox="0 0 12 12"><circle cx="6" cy="6" r="5.5"/><path d="M3 3.5 Q5 2.5 5.5 4.5 Q4 6 5.5 7.5 L4.5 10 Q2 8 3 3.5 Z M7.5 2.5 Q9.5 4 8 6.5 Q7 5.5 7.5 2.5 Z" fill="#f7f7f7"/></svg>
    </li>
  </ul>
</section>

</body>
</html>
```